Residential Remodeling Contractor needs updated business card

I need a new design for my business card.
Name of the company is Ridgefell Construction. I need a card that commands presence, strength, integrity. I have been in business for 28 years. I am a Residential Remodeling Contractor that covers all aspects of a residential remodel and build.

```html
<!DOCTYPE html>
<html lang="en">
<head>
<meta charset="utf-8">
<title>Ridgefell Construction – Business Card</title>
<link rel="stylesheet" href="https://fonts.googleapis.com/css2?family=Cinzel:wght@700&family=Arimo:wght@400&display=swap">
<style>
  :root {
    --backdrop: #1e1f22;
    --card-blue: #1b4185;
    --card-blue-deep: #163672;
    --ink-white: #ffffff;
    --ink-soft: #e6ecf6;
    --card-radius: 18px;
  }
  * { box-sizing: border-box; margin: 0; padding: 0; }
  html, body {
    width: 1200px;
    height: 801px;
    overflow: hidden;
    background: var(--backdrop);
  }
  .canvas {
    width: 1200px;
    height: 801px;
    display: flex;
    align-items: center;
    justify-content: center;
    gap: 48px;
  }
  .card {
    position: relative;
    width: 530px;
    height: 302px;
    border-radius: var(--card-radius);
    background: linear-gradient(135deg, var(--card-blue) 0%, var(--card-blue-deep) 100%);
    color: var(--ink-white);
    overflow: hidden;
    box-shadow: 0 18px 40px rgba(0, 0, 0, 0.55);
  }

  /* Shared wordmark */
  .wordmark {
    display: flex;
    align-items: center;
    gap: 12px;
    font-family: "Cinzel", Georgia, serif;
    font-weight: 700;
    color: var(--ink-white);
    line-height: 1.02;
  }
  .wordmark__square {
    flex: none;
    background: var(--ink-white);
  }

  /* Details side */
  .card--details .wordmark {
    position: absolute;
    left: 34px;
    top: 48px;
    font-size: 25px;
  }
  .card--details .wordmark__square { width: 14px; height: 14px; }

  .person {
    position: absolute;
    left: 34px;
    bottom: 46px;
  }
  .person__name {
    font-family: "Cinzel", Georgia, serif;
    font-weight: 700;
    font-size: 21px;
    letter-spacing: 0.5px;
  }
  .person__title {
    margin-top: 4px;
    font-family: "Arimo", Arial, sans-serif;
    font-size: 13px;
    color: var(--ink-soft);
  }

  .contact {
    position: absolute;
    right: 30px;
    top: 62px;
    width: 230px;
    font-family: "Arimo", Arial, sans-serif;
    font-size: 12.5px;
    line-height: 1.55;
    color: var(--ink-soft);
  }
  .contact__address { margin-bottom: 12px; }
  .contact__list { list-style: none; }
  .contact__item {
    display: flex;
    align-items: center;
    gap: 8px;
  }
  .contact__icon {
    width: 11px;
    height: 11px;
    flex: none;
    fill: var(--ink-white);
  }

  /* Brand side */
  .card--brand {
    display: flex;
    align-items: center;
    justify-content: center;
  }
  .card--brand .wordmark {
    font-size: 42px;
    gap: 18px;
  }
  .card--brand .wordmark__square { width: 22px; height: 22px; }
</style>
</head>
<body>
<main class="canvas">

  <section class="card card--details" aria-label="Business card, details side">
    <div class="wordmark">
      <span class="wordmark__square"></span>
      <span class="wordmark__name">Ridgefell<br>Construction</span>
    </div>

    <div class="person">
      <p class="person__name">Daniel Okafor</p>
      <p class="person__title">Owner &amp; Manager</p>
    </div>

    <address class="contact">
      <p class="contact__address">P.O. Box 410 Harlow Street<br>Calder AB, T2B 4K1</p>
      <ul class="contact__list">
        <li class="contact__item">
          <svg class="contact__icon" viewBox="0 0 24 24" aria-hidden="true"><path d="M6.6 10.8a15.2 15.2 0 0 0 6.6 6.6l2.2-2.2a1 1 0 0 1 1-.25 11.4 11.4 0 0 0 3.6.57 1 1 0 0 1 1 1V20a1 1 0 0 1-1 1A17 17 0 0 1 3 4a1 1 0 0 1 1-1h3.5a1 1 0 0 1 1 1c0 1.25.2 2.45.57 3.57a1 1 0 0 1-.25 1z"/></svg>
          <span>555 214 7730</span>
        </li>
        <li class="contact__item">
          <svg class="contact__icon" viewBox="0 0 24 24" aria-hidden="true"><path d="M2 5h20v14H2z M2 5l10 8 10-8" fill="none" stroke="#fff" stroke-width="2.4"/></svg>
          <span>info@ridgefellbuild.com</span>
        </li>
        <li class="contact__item">
          <svg class="contact__icon" viewBox="0 0 24 24" aria-hidden="true"><circle cx="12" cy="12" r="10" fill="none" stroke="#fff" stroke-width="2.4"/><path d="M2 12h20M12 2c3 3 3 17 0 20M12 2c-3 3-3 17 0 20" fill="none" stroke="#fff" stroke-width="2"/></svg>
          <span>www.ridgefellbuild.com</span>
        </li>
      </ul>
    </address>
  </section>

  <section class="card card--brand" aria-label="Business card, brand side">
    <div class="wordmark">
      <span class="wordmark__square"></span>
      <span class="wordmark__name">Ridgefell<br>Construction</span>
    </div>
  </section>

</main>
</body>
</html>
```